Business Card Design Project - del varosi group

dear Sirs

we need business card design for our group ( DEL Varosi Group ) , i have got the Logo design of our group from pixel harbor in previous , so all need details relating to our group i think available with you, as well as the the chosen logo design

we hope to provide us with business card logo that to be appropaite and satisfactory to us .

thanks

note : logo design of our group is attached .
Updates

Reason: please extend the deadline of my project for additional 15 days because i didn't received appropriate design for our gruop yet . kindly beaware that i have received 77 design till now , supossed to send me 200-250 design at least . thanks

Target Market(s)

contents

name : Kerem EL Nadiri

position : Operation Manager

Industry/Entity Type

Business

Requirements
Must have

• person name

group logo
Nice to have
• logo color matching with back background

```html
<!DOCTYPE html>
<html lang="en">
<head>
<meta charset="utf-8">
<title>DEL Varosi Group – Business Card</title>
<link rel="stylesheet" href="https://fonts.googleapis.com/css2?family=Open+Sans:wght@400;600;700&display=swap">
<style>
  :root {
    --bg: #ececec;
    --card-white: #ffffff;
    --brand-blue: #0b4f92;
    --accent-blue: #1f7dcb;
    --ink-grey: #555a60;
    --on-blue: #ffffff;
  }
  * { box-sizing: border-box; margin: 0; padding: 0; }
  html, body { width: 1200px; height: 758px; overflow: hidden; }
  body {
    background: var(--bg);
    font-family: "Open Sans", Arial, sans-serif;
    position: relative;
  }
  .card {
    position: absolute;
    top: 222px;
    width: 540px;
    height: 315px;
    border-radius: 22px;
    overflow: hidden;
    box-shadow: 0 6px 18px rgba(0,0,0,0.18);
  }
  .card-front { left: 40px; background: var(--card-white); }
  .card-back { left: 620px; background: var(--brand-blue); }

  .front-waves { position: absolute; inset: 0; width: 540px; height: 315px; }

  .brand {
    position: absolute;
    display: flex;
    align-items: center;
    gap: 12px;
    font-weight: 700;
    letter-spacing: 1px;
    white-space: nowrap;
  }
  .brand-mark { display: block; border: 4px solid currentColor; }
  .card-front .brand {
    left: 110px; top: 46px;
    font-size: 40px;
    color: var(--brand-blue);
  }
  .card-front .brand-mark { width: 34px; height: 34px; }
  .card-back .brand {
    left: 90px; top: 118px;
    font-size: 40px;
    color: var(--on-blue);
  }
  .card-back .brand-mark { width: 34px; height: 34px; }

  .address {
    position: absolute;
    left: 0; right: 0; top: 132px;
    text-align: center;
    font-size: 13px;
    color: var(--ink-grey);
    letter-spacing: 0.4px;
  }

  .person {
    position: absolute;
    left: 150px; top: 228px;
    text-align: center;
    color: var(--on-blue);
  }
  .person-name { font-size: 17px; font-weight: 700; }
  .person-role { font-size: 12.5px; margin-top: 1px; }
  .person-web { font-size: 12.5px; margin-top: 6px; }

  .divider {
    position: absolute;
    left: 304px; top: 214px;
    width: 1px; height: 78px;
    background: rgba(255,255,255,0.6);
  }

  .contacts {
    position: absolute;
    left: 316px; top: 210px;
    list-style: none;
    color: var(--on-blue);
    font-size: 12.5px;
    line-height: 20px;
  }
  .contacts li { display: flex; align-items: center; gap: 6px; }
  .contacts svg { width: 10px; height: 10px; fill: var(--on-blue); flex: none; }

  .back-web {
    position: absolute;
    left: 0; right: 0; top: 232px;
    text-align: center;
    color: var(--on-blue);
    font-size: 19px;
    letter-spacing: 1.5px;
  }
</style>
</head>
<body>

<section class="card card-front">
  <svg class="front-waves" viewBox="0 0 540 315" aria-hidden="true">
    <path d="M0 158 Q260 232 540 98 L540 315 L0 315 Z" fill="var(--accent-blue)"/>
    <path d="M0 176 Q270 250 540 116 L540 315 L0 315 Z" fill="var(--card-white)"/>
    <path d="M0 180 Q270 254 540 120 L540 315 L0 315 Z" fill="var(--brand-blue)"/>
  </svg>

  <div class="brand"><span class="brand-mark"></span>DEL Varosi Group</div>
  <p class="address">Street name, City, State, zip code</p>

  <div class="person">
    <p class="person-name">Kerem EL Nadiri</p>
    <p class="person-role">Operation Manager</p>
    <p class="person-web">www.website.com</p>
  </div>

  <span class="divider"></span>

  <ul class="contacts">
    <li><svg viewBox="0 0 10 10"><rect x="2.5" y="0" width="5" height="10" rx="1"/></svg>+2347031184520</li>
    <li><svg viewBox="0 0 10 10"><path d="M2 0 L4 2.5 L3 4 Q4.5 6 6 7 L7.5 6 L10 8 L8.5 10 Q2 9 0 1.5 Z"/></svg>+2347031184520</li>
    <li><svg viewBox="0 0 10 10"><circle cx="5" cy="3" r="2.6"/><path d="M0 10 Q0 6 5 6 Q10 6 10 10 Z"/></svg>+2347031184520</li>
    <li><svg viewBox="0 0 10 10"><path d="M0 2 H10 V8.5 H0 Z M0 2 L5 6 L10 2" /></svg>name@northbayhotels.com</li>
  </ul>
</section>

<section class="card card-back">
  <div class="brand"><span class="brand-mark"></span>DEL Varosi Group</div>
  <p class="back-web">www.website.com</p>
</section>

</body>
</html>
```